Business card design for my company.
I would like the card's background colour to be black. You can also see our web site to get an idea of our brand. https://www.tmwhomecrafting.com.au/
- Name
- Email

```html
<!DOCTYPE html>
<html lang="en">
<head>
<meta charset="utf-8">
<title>TMW Home Crafting – Business Card</title>
<link href="https://fonts.googleapis.com/css2?family=Arimo:wght@400;700&display=swap" rel="stylesheet">
<style>
  :root {
    --backdrop: #e6e6e6;
    --charcoal: #2f2f2f;
    --green: #0d9444;
    --white: #ffffff;
    --rule: #1a1a1a;
  }
  * { margin: 0; padding: 0; box-sizing: border-box; }
  html, body {
    width: 1200px; height: 1200px; overflow: hidden;
    background: var(--backdrop);
    font-family: "Arimo", Arial, sans-serif;
    color: var(--white);
  }
  .canvas { position: relative; width: 1200px; height: 1200px; }

  .card { position: absolute; overflow: hidden; }
  .card--front { left: 266px; top: 158px; width: 689px; height: 394px; background: var(--green); }
  .card--back { left: 262px; top: 653px; width: 686px; height: 392px; background: var(--green); }

  .front__head {
    position: absolute; left: 0; top: 0; width: 100%; height: 221px;
    background: var(--charcoal);
    display: flex; align-items: center; justify-content: center;
  }
  .front__stripe {
    position: absolute; left: 0; top: 221px; width: 100%; height: 8px;
    background: var(--white); border-bottom: 2px solid var(--rule);
  }

  .brand-name {
    font-weight: 700; color: var(--white); letter-spacing: 1px;
    text-align: center; line-height: 1.1; text-transform: uppercase;
    white-space: nowrap;
  }
  .front__head .brand-name { font-size: 25px; }
  .back__body {
    position: absolute; inset: 0;
    display: flex; align-items: center; justify-content: center;
  }
  .back__body .brand-name { font-size: 33px; }

  .identity {
    position: absolute; right: 335px; top: 262px; text-align: right;
  }
  .identity__name { font-size: 25px; font-weight: 700; line-height: 1; letter-spacing: 0.3px; }
  .identity__role, .identity__address { font-size: 15px; line-height: 21px; white-space: nowrap; }
  .identity__role { margin-top: 6px; }

  .divider {
    position: absolute; left: 370px; top: 263px; width: 1px; height: 95px;
    background: var(--white); opacity: 0.85;
  }

  .contacts { position: absolute; left: 388px; top: 270px; list-style: none; }
  .contacts li {
    display: flex; align-items: center; gap: 9px;
    font-size: 15.5px; height: 20.3px; white-space: nowrap;
  }
  .contacts svg { width: 13px; height: 13px; fill: var(--white); flex: none; }
</style>
</head>
<body>
<div class="canvas">

  <section class="card card--front" aria-label="Card front">
    <div class="front__head">
      <p class="brand-name">TMW Home Crafting</p>
    </div>
    <div class="front__stripe"></div>

    <div class="identity">
      <p class="identity__name">DANIEL HART</p>
      <p class="identity__role">President</p>
      <p class="identity__address">4152 Wattle Grove</p>
      <p class="identity__address">Ridgefield, Canada 34570</p>
    </div>

    <div class="divider"></div>

    <ul class="contacts">
      <li>
        <svg viewBox="0 0 24 24" aria-hidden="true"><path d="M6.6 10.8a15.1 15.1 0 0 0 6.6 6.6l2.2-2.2c.3-.3.7-.4 1-.2 1.1.4 2.3.6 3.6.6.6 0 1 .4 1 1V20c0 .6-.4 1-1 1A17 17 0 0 1 3 4c0-.6.4-1 1-1h3.5c.6 0 1 .4 1 1 0 1.3.2 2.5.6 3.6.1.3 0 .7-.2 1z"/></svg>
        <span>736-402-1187</span>
      </li>
      <li>
        <svg viewBox="0 0 24 24" aria-hidden="true"><path d="M7 1h10a2 2 0 0 1 2 2v18a2 2 0 0 1-2 2H7a2 2 0 0 1-2-2V3a2 2 0 0 1 2-2zm0 3v14h10V4zm5 15.5a1 1 0 1 0 0 2 1 1 0 0 0 0-2z"/></svg>
        <span>736-519-2046</span>
      </li>
      <li>
        <svg viewBox="0 0 24 24" aria-hidden="true"><path d="M2 5h20v14H2zm2 2v.5l8 5.5 8-5.5V7zm0 3v7h16v-7l-8 5.5z"/></svg>
        <span>info@tmwcraft.example</span>
      </li>
      <li>
        <svg viewBox="0 0 24 24" aria-hidden="true"><path d="M12 2a10 10 0 1 0 0 20 10 10 0 0 0 0-20zm-1 17.9A8 8 0 0 1 4.2 10L9 15v1a2 2 0 0 0 2 2zm6.9-2.5A2 2 0 0 0 16 16h-1v-3a1 1 0 0 0-1-1H8v-2h2a1 1 0 0 0 1-1V7h2a2 2 0 0 0 2-2v-.4a8 8 0 0 1 2.9 12.8z"/></svg>
        <span>www.tmwcraft.example</span>
      </li>
    </ul>
  </section>

  <section class="card card--back" aria-label="Card back">
    <div class="back__body">
      <p class="brand-name">TMW Home Crafting</p>
    </div>
  </section>

</div>
</body>
</html>
```